Fresh, modern, fun business card for pediatric dental practice

Need a business card for fresh, modern, fun pediatric dental practice

Clean look that matches our website's font and colors

We prefer the look of curved corners on business cards

Target Market(s)

parents (mothers) of young children, professionals, mid-high class

Industry/Entity Type

Dental

Contact Information for Business Card

Maplebrook Pediatric Dentistry
482 Quarry Lane
Suite 517
Fernvale, PA 17590
717.555.0193
www.maplebrookkidsdental.example

Mei-Ran Tsai, DMD
Corinne Walbeck, DMD
(we are working on our email address, but we would like that on the card as well)

Font styles to use
Sans Serif

Requirements
Must have
• All info; we would also like to make cards for individual staff members
• colors from our website and color palatte, attatched
• use same font and design as website for branding
Nice to have
• clean, simple card that has a pop of color
• we would like to see a few designs with our tag line "where smiles get brighter"
• we are not sure if we want to have it on there or not
• we would like to see a few designs incorporating the ribbon graphic on our website where the word WELCOME is

```html
<!DOCTYPE html>
<html lang="en">
<head>
<meta charset="utf-8">
<title>Maplebrook Pediatric Dentistry – Business Card</title>
<link rel="stylesheet" href="https://fonts.googleapis.com/css2?family=Ubuntu:wght@500;700&family=Roboto:wght@400&display=swap">
<style>
  :root {
    --page: #c4c4c4;
    --card: #4c2f4b;
    --gold: #e5a60c;
    --pink: #d94c8e;
    --ink-light: #ece6ec;
    --shadow: rgba(0, 0, 0, 0.28);
  }
  * { margin: 0; padding: 0; box-sizing: border-box; }
  html, body {
    width: 1200px;
    height: 576px;
    overflow: hidden;
    background: var(--page);
  }
  .canvas {
    position: relative;
    width: 1200px;
    height: 576px;
  }
  .card {
    position: absolute;
    top: 138px;
    width: 484px;
    height: 294px;
    border-radius: 14px;
    background: var(--card);
    box-shadow: 2px 3px 6px var(--shadow);
    overflow: hidden;
  }
  .card--front { left: 82px; }
  .card--back { left: 602px; width: 480px; }

  /* Wordmark: one colour, one weight */
  .wordmark {
    font-family: "Ubuntu", sans-serif;
    font-weight: 500;
    color: var(--gold);
    line-height: 1;
  }
  .wordmark__main { display: block; }
  .wordmark__sub { display: block; }

  /* Front */
  .front-mark {
    position: absolute;
    left: 50%;
    top: 58px;
    width: 52px;
    height: 52px;
    margin-left: -26px;
    border-radius: 50%;
    background: var(--gold);
  }
  .front-wordmark {
    position: absolute;
    left: 0;
    right: 0;
    top: 126px;
    text-align: center;
  }
  .front-wordmark .wordmark__main { font-size: 44px; letter-spacing: 1px; }
  .front-wordmark .wordmark__sub { font-size: 25px; letter-spacing: 1.5px; margin-top: 6px; }
  .front-url {
    position: absolute;
    left: 0;
    right: 0;
    top: 266px;
    text-align: center;
    font-family: "Roboto", sans-serif;
    font-size: 12.5px;
    letter-spacing: 0.3px;
    color: var(--ink-light);
  }
  .front-url .accent { color: var(--gold); }
  .front-url__rule {
    position: absolute;
    top: 275px;
    width: 46px;
    height: 2px;
    background: linear-gradient(90deg, transparent, var(--pink) 30%, var(--pink) 70%, transparent);
  }
  .front-url__rule--left { left: 84px; }
  .front-url__rule--right { right: 84px; }

  /* Back */
  .back-wordmark {
    position: absolute;
    left: 20px;
    top: 30px;
  }
  .back-wordmark .wordmark__main { font-size: 32px; letter-spacing: 1px; }
  .back-wordmark .wordmark__sub { font-size: 17px; letter-spacing: 1px; margin-top: 5px; }
  .back-decoration {
    position: absolute;
    left: 302px;
    top: 76px;
    width: 176px;
    height: 176px;
    border-radius: 50%;
    border: 12px solid var(--gold);
  }
  .person {
    position: absolute;
    left: 20px;
    top: 158px;
    font-family: "Ubuntu", sans-serif;
    font-weight: 700;
    font-size: 17px;
    color: var(--gold);
  }
  .address {
    position: absolute;
    left: 20px;
    top: 187px;
    font-family: "Roboto", sans-serif;
    font-size: 12.5px;
    line-height: 16px;
    color: var(--ink-light);
    font-style: normal;
  }
  .contact-list {
    position: absolute;
    left: 20px;
    top: 227px;
    list-style: none;
    font-family: "Roboto", sans-serif;
    font-size: 12.5px;
    color: var(--ink-light);
  }
  .contact-list li {
    display: flex;
    align-items: center;
    height: 16px;
  }
  .contact-list .icon {
    width: 10px;
    height: 10px;
    margin-right: 8px;
    flex: none;
  }
  .contact-list .accent { color: var(--pink); }
</style>
</head>
<body>
<main class="canvas">

  <section class="card card--front" aria-label="Card front">
    <span class="front-mark" aria-hidden="true"></span>
    <h1 class="wordmark front-wordmark">
      <span class="wordmark__main">maplebrook</span>
      <span class="wordmark__sub">pediatric dentistry</span>
    </h1>
    <span class="front-url__rule front-url__rule--left" aria-hidden="true"></span>
    <p class="front-url">www.<span class="accent">maplebrookkidsdental</span>.example</p>
    <span class="front-url__rule front-url__rule--right" aria-hidden="true"></span>
  </section>

  <section class="card card--back" aria-label="Card back">
    <h2 class="wordmark back-wordmark">
      <span class="wordmark__main">maplebrook</span>
      <span class="wordmark__sub">pediatric dentistry</span>
    </h2>
    <span class="back-decoration" aria-hidden="true"></span>

    <p class="person">Corinne Walbeck, DMD</p>
    <address class="address">
      482 Quarry Lane<br>
      Suite 517 Fernvale, PA 17590
    </address>
    <ul class="contact-list">
      <li>
        <svg class="icon" viewBox="0 0 10 10" aria-hidden="true">
          <path d="M1 3.2C1 2 2 1.5 5 1.5S9 2 9 3.2L7.4 3.8 6.8 3H3.2L2.6 3.8Z M2.6 4.4h4.8L8.5 8.5h-7Z" fill="#ece6ec"/>
          <circle cx="5" cy="6.4" r="1" fill="#4c2f4b"/>
        </svg>
        717.555.0193
      </li>
      <li>
        <svg class="icon" viewBox="0 0 10 10" aria-hidden="true">
          <rect x="0.5" y="2" width="9" height="6.5" fill="#ece6ec"/>
          <path d="M0.8 2.3 5 5.8 9.2 2.3" fill="none" stroke="#4c2f4b" stroke-width="0.9"/>
        </svg>
        name@maplebrookkidsdental.example
      </li>
      <li>
        <svg class="icon" viewBox="0 0 10 10" aria-hidden="true">
          <g fill="none" stroke="#ece6ec" stroke-width="0.9">
            <circle cx="5" cy="5" r="4"/>
            <ellipse cx="5" cy="5" rx="1.8" ry="4"/>
            <path d="M1 5h8"/>
          </g>
        </svg>
        <span>www.<span class="accent">maplebrookkidsdental</span>.example</span>
      </li>
    </ul>
  </section>

</main>
</body>
</html>
```